Brightfen Business Card Redesign & Logo Update

We need to update our business cards to something more modern and fresh. Brightfen can provide the current color schemes and old design examples, but welcome creativity in helping us with this redesign. PLEASE NOTE that we no longer utilize the "tree" and/or "leaf" imagery in our branding. If able would apprecaite an update on the quality of our "words only" logo in Ai. / PNG formats too.

Target Market(s)

Investors, landowners, corporate partners, contractors

Industry/Entity Type

Environmental Restoration & Conservation

Contact Information for Business Card

Logo, persons name, title, mailing address, phone and email, website url

Font styles to use
Other font styles liked:
• Merriweather

Requirements
Nice to have
• Logo, persons name, title, mailing address, phone and email, website url, but open to ideams
Should not have
• No all back backgrounds

```html
<!DOCTYPE html>
<html lang="en">
<head>
<meta charset="utf-8">
<title>Brightfen Business Card</title>
<link href="https://fonts.googleapis.com/css2?family=Merriweather:wght@400;700;900&display=swap" rel="stylesheet">
<style>
  :root {
    --stage: #8a8a8c;
    --card-light: #ffffff;
    --card-back: #1e4a30;
    --ink: #2b2b2b;
    --accent-orange: #f7821b;
    --accent-green: #14873c;
    --accent-green-light: #5cbf7c;
    --on-dark: #ffffff;
  }
  * { box-sizing: border-box; margin: 0; padding: 0; }
  html, body { width: 1200px; height: 781px; overflow: hidden; }
  body {
    background: var(--stage);
    font-family: "Merriweather", Georgia, serif;
    position: relative;
  }
  .card {
    position: absolute;
    border-radius: 20px;
    box-shadow: 0 10px 24px rgba(0,0,0,0.25);
  }
  .card--front {
    left: 190px; top: 140px;
    width: 286px; height: 500px;
    background: var(--card-light); color: var(--ink);
  }
  .card--back {
    left: 540px; top: 160px;
    width: 500px; height: 286px;
    background: var(--card-back); color: var(--on-dark);
  }

  .wordmark { font-weight: 900; line-height: 1; letter-spacing: 1px; }
  .tagline { font-weight: 700; text-transform: uppercase; }

  .card--front .brand { position: absolute; left: 26px; top: 30px; }
  .card--front .wordmark { font-size: 29px; color: var(--accent-green); }
  .card--front .tagline { font-size: 8px; letter-spacing: 1px; margin-top: 6px; color: var(--ink); }

  .contact { position: absolute; left: 26px; bottom: 30px; }
  .contact__name { font-weight: 700; font-size: 16px; letter-spacing: 1px; }
  .contact__title { font-size: 11px; color: var(--accent-orange); margin-top: 3px; }
  .contact__address { font-size: 11px; line-height: 17px; margin-top: 10px; }
  .contact__lines { list-style: none; margin-top: 10px; }
  .contact__lines li { display: flex; align-items: center; gap: 8px; font-size: 11px; line-height: 19px; }
  .contact__lines svg { width: 11px; height: 11px; flex: none; }

  .card--back .brand { position: absolute; left: 0; right: 0; top: 90px; text-align: center; }
  .card--back .wordmark { font-size: 48px; color: var(--accent-orange); }
  .card--back .tagline { font-size: 11px; letter-spacing: 2px; margin-top: 8px; }
  .social { position: absolute; left: 0; right: 0; top: 198px; display: flex; justify-content: center; gap: 12px; }
  .social span { width: 20px; height: 20px; border-radius: 50%; background: var(--accent-green-light); }
  .social span:nth-child(2) { background: var(--accent-orange); }
</style>
</head>
<body>
  <section class="card card--front">
    <div class="brand">
      <div class="wordmark">BRIGHTFEN</div>
      <div class="tagline">Environmental Credit Company</div>
    </div>
    <div class="contact">
      <div class="contact__name">DARA ELLISON</div>
      <div class="contact__title">Director</div>
      <div class="contact__address">4821 County Road 58,<br>Harlow, TX 75990</div>
      <ul class="contact__lines">
        <li>
          <svg viewBox="0 0 10 10" aria-hidden="true"><path d="M2 1l2 0 1 2.5-1.2 1a5 5 0 0 0 2.7 2.7l1-1.2L10 7v2l-1 1C4.5 10 0 5.5 0 1z" fill="var(--accent-green)"/></svg>
          (555) 014-2287
        </li>
        <li>
          <svg viewBox="0 0 10 10" aria-hidden="true"><rect x="0" y="2" width="10" height="7" rx="1" fill="var(--accent-green)"/><path d="M0.5 2.5L5 6l4.5-3.5" stroke="#fff" stroke-width="1" fill="none"/></svg>
          info@brightfencredits.com
        </li>
        <li>
          <svg viewBox="0 0 10 10" aria-hidden="true"><circle cx="5" cy="5" r="4.5" fill="var(--accent-green)"/><path d="M0.5 5h9M5 0.5c-2.4 2.6-2.4 6.4 0 9M5 0.5c2.4 2.6 2.4 6.4 0 9" stroke="#fff" stroke-width="0.8" fill="none"/></svg>
          www.brightfencredits.com
        </li>
      </ul>
    </div>
  </section>

  <section class="card card--back">
    <div class="brand">
      <div class="wordmark">BRIGHTFEN</div>
      <div class="tagline">Environmental Credit Company</div>
    </div>
    <div class="social" aria-label="Social profiles">
      <span></span><span></span><span></span>
    </div>
  </section>
</body>
</html>
```